Aunt Wilma's Ember-Kissed Husk Shack Concession Trailer Logo Wraps

Looking to put my design concept into a final production-ready format for vinyl-based logo "wrap" on the exterior of a 7x12 black concession trailer selling farm-fresh corn on the cob slathered in flavor flamboyance, corn in a cup, corn over crushed snacks (Crunvels, Zaplins, Puffnars, etc.) served in the bags, fire-roasted street corn (Mexican elotes), corn grits, corn chowder, cornbread, corndogs. I have my fonts and colors and a flame graphic I've roughly edited/reworked attempting to make it work and need a design pro to bring it all together for me. The approximate size of the graphics on the four sides of the trailer will be: the serving window when closed (48"L x 24"H); front (48"x48"); full right side (11'x5'); door (6'x2') and possibly the left side next to door (3'x5'). Pictures uploaded.
Target Market(s)
Food truck festivals, private catering gigs, fairs, farm markets, concerts, etc.
Font styles to use
Other font styles liked:
- flame fetish, Algerian
Requirements
Must have
- My color scheme as depicted in uploaded files, flame fetish font uploaded (will consider similar fonts), flame/fire artwork, bright bold colors that pop against a black background
Nice to have
- straight line of flames on each side of the "fire-roasted" text, flowing from the first and last letter

```html
<!DOCTYPE html>
<html lang="en">
<head>
<meta charset="utf-8">
<title>Aunt Wilma's Ember-Kissed Husk Shack — Trailer Wrap</title>
<link rel="stylesheet" href="https://fonts.googleapis.com/css2?family=Lobster&family=Kaushan+Script&family=Alfa+Slab+One&display=swap">
<style>
  :root {
    --night: #000000;
    --band: rgba(14, 14, 14, 0.9);
    --band-edge: rgba(60, 55, 10, 0.55);
    --sky-blue: #1496d6;
    --corn-yellow: #f5e11a;
    --butter-gold: #f4bb12;
    --ember-orange: #ff8a1c;
    --flame-red: #c8260a;
  }
  * { margin: 0; padding: 0; box-sizing: border-box; }
  html, body {
    width: 1200px; height: 600px; overflow: hidden;
    background: var(--night);
  }
  .wrap-panel {
    position: relative;
    width: 1200px; height: 600px;
    background: var(--night);
    overflow: hidden;
  }
  .flame-artwork {
    position: absolute;
    left: 0; top: 120px;
    width: 1200px; height: 300px;
    background:
      radial-gradient(ellipse 240px 190px at 40px 230px, rgba(255,210,58,.9), rgba(255,122,16,.65) 45%, transparent 75%),
      radial-gradient(ellipse 280px 210px at 1150px 220px, rgba(255,210,58,.95), rgba(255,122,16,.65) 45%, transparent 75%),
      radial-gradient(ellipse 460px 70px at 600px 215px, rgba(255,150,30,.7), rgba(200,38,10,.4) 55%, transparent 80%),
      radial-gradient(ellipse 700px 90px at 600px 230px, rgba(200,38,10,.55), transparent 80%),
      linear-gradient(to bottom, transparent 0%, rgba(200,38,10,.12) 45%, rgba(255,122,16,.3) 75%, rgba(255,122,16,.1) 100%);
  }
  .menu-band {
    position: absolute;
    left: 0; top: 346px;
    width: 1200px; height: 176px;
    background: linear-gradient(to bottom, var(--band-edge) 0px, var(--band) 24px, var(--band) 100%);
  }
  .brand-owner {
    position: absolute;
    left: 0; top: 48px; width: 1200px;
    text-align: center;
    font-family: "Lobster", cursive;
    font-weight: 400;
    font-size: 138px; line-height: 1;
    color: var(--sky-blue);
  }
  .brand-style {
    position: absolute;
    left: 0; top: 236px; width: 1200px;
    text-align: center;
    font-family: "Kaushan Script", cursive;
    font-size: 92px; line-height: 1.1;
    color: var(--ember-orange);
  }
  .brand-product {
    position: absolute;
    left: 0; top: 370px; width: 1200px;
    text-align: center;
    font-family: "Alfa Slab One", serif;
    font-size: 96px; line-height: 1.05;
    letter-spacing: 8px;
    color: var(--corn-yellow);
  }
  .tagline {
    position: absolute;
    left: 0; top: 490px; width: 1200px;
    text-align: center;
    font-family: "Kaushan Script", cursive;
    font-size: 36px; line-height: 1.2;
    color: var(--butter-gold);
  }
</style>
</head>
<body>
  <main class="wrap-panel">
    <div class="flame-artwork" role="img" aria-label="Row of orange and yellow fire flames with sparks across the panel"></div>
    <div class="menu-band"></div>
    <h1 class="brand-owner">Aunt Wilma's</h1>
    <p class="brand-style">ember-kissed</p>
    <p class="brand-product">HUSK SHACK</p>
    <p class="tagline">Sweet corn on the cob dressed in bold, smoky spice</p>
  </main>
</body>
</html>
```